Beauty Salon Mentor Illustration

Hi There, I'm Belinda and I'm a Beauty Salon owner mentor. We are needing 5 different illustration design for a beauty salon coaching business. The pictures will be used on our website next to a small description about our course out line.
Course and what the illustrations will be referring to below:
1. Launch Pad Parlour -Make your dream of owning a salon a reality.
Three options of start-up training and support, teaching must-know insights for beauty therapists who are ready to take the leap to salon owner and want to do it right. Whether you’ve been in the beauty industry a short time or forever, Launch Pad Parlour will set you up for salon success.

2. Chairs Filled Fast - Attract more clients with simple, strategic digital marketing. Chairs Filled Fast educates on the ins and outs of sponsored social media ads. With easy-to-follow video training, you’ll establish your online presence and increase salon bookings.
Learn how to show up on social media with effective strategies that work. Choose our Handled Entirely system, or learn to do it all with our DIY system.

3. Momentum Studio Plan - Transform your salon and your life. Our most tailored program, Momentum Studio Plan offers coaching memberships with Bloom Beauty Hub’s Founder- Belinda. With our results focused framework, you will upskill employees, improve the working environment of the salon and receive leading beauty industry training as we dive into the culture and mindset of your salon. With Belinda as your business mentor and biggest cheerleader get ready to achieve your business goals and move forward with rapid growth.

4. Revive Parlour Path - Successfully put your salon back on the map.
Step into today’s beauty landscape with optimised marketing and industry expertise. If your salon’s been open for a year or even twenty years, Revive Parlour Path will elevate your business, renew your love for your salon and set you up to generate more income. Stand out from the competition as you increase online presence, learn key business development processes and see real results.

5. Skillset Studio Plan - Successfully Upskill and Level Up Your Salon. Skillset Studio Plan offers three training options- In Salon, Online & Diploma of Beauty Therapy. Whether you have your own salon or want to become qualified, Bloom Beauty Hub’s- Skillset Studio Plan adds industry authority and brings specialist expertise to all level of beauty therapists.
Our coaching is based in Australia, aim at female beauty salon owners who are ready to take their business to the next level.

In the files below is just a picture of me so you know who i am. We are wanting the illusion to appeal to a wide audience.

I am the business and everyone i attract into our coaching program works closely with me.

Target Market(s)

Beauty Salon owners; women

Font styles to use
Sans Serif

Colors
fce8d3
fee3d4
fff5ef
fff3d1
f9bb94
fcca95

Requirements
Must have
• Must be relatable to the brief, designs must look great together on the website or separately on their own.
Nice to have
• Industry relatable, engaging to the eye.
Should not have
• i would prefer if there wasn't any words on the illusion

```html
<!DOCTYPE html>
<html lang="en">
<head>
<meta charset="utf-8">
<title>Bloom Beauty Hub – Mobile Pages</title>
<link href="https://fonts.googleapis.com/css2?family=EB+Garamond:wght@400;500&family=Playfair+Display:ital@1&family=Raleway:wght@400&family=Montserrat:wght@500&display=swap" rel="stylesheet">
<style>
  :root {
    --bg: #f2e3dc;
    --band: #e8d1c2;
    --paper: #ffffff;
    --blush-strip: #fdf3ee;
    --ink: #1f1b19;
    --ink-soft: #2b2624;
    --logo: #3a3330;
    --art-light: #efe9e4;
    --art-mid: #dcc6b6;
    --art-deep: #c9ab94;
  }
  * { box-sizing: border-box; margin: 0; padding: 0; }
  html, body { width: 1200px; height: 1198px; overflow: hidden; background: var(--bg); }
  .stage { position: relative; width: 1200px; height: 1198px; }
  .screen {
    position: absolute; top: 84px; width: 500px; height: 1030px;
    background: var(--paper); border-radius: 40px; overflow: hidden;
  }
  .screen--home { left: 60px; }
  .screen--about { left: 640px; }

  /* home screen */
  .site-header { height: 134px; display: flex; align-items: center; justify-content: center; position: relative; }
  .brand { font-family: "Montserrat", sans-serif; font-weight: 500; font-size: 15px; letter-spacing: 1.5px; color: var(--logo); }
  .menu-icon { position: absolute; right: 38px; top: 50px; }
  .hero-band { background: var(--band); padding: 58px 20px 24px; text-align: center; }
  .hero-title { font-family: "EB Garamond", serif; font-weight: 400; font-size: 42px; color: #fff; letter-spacing: 0.5px; }
  .hero-sub { font-family: "Playfair Display", serif; font-style: italic; font-size: 25px; line-height: 42px; color: var(--ink); margin-top: 26px; }
  .hero-art {
    height: 455px;
    background: linear-gradient(100deg, var(--art-mid) 0%, var(--art-light) 45%, var(--art-light) 75%, var(--art-deep) 100%);
  }

  /* about screen */
  .top-strip { height: 72px; background: var(--blush-strip); }
  .feature-band { background: var(--band); height: 345px; text-align: center; padding-top: 22px; }
  .feature-art {
    width: 170px; height: 170px; margin: 0 auto; border-radius: 50%;
    border: 5px solid #fff;
    background: linear-gradient(120deg, var(--art-mid), var(--art-light) 60%, var(--art-deep));
  }
  .feature-title { font-family: "EB Garamond", serif; font-weight: 500; font-size: 28px; color: var(--ink); margin-top: 14px; letter-spacing: 0.3px; }
  .feature-text { font-family: "EB Garamond", serif; font-size: 23px; line-height: 36px; color: var(--ink); margin: 14px 40px 0; }
  .about { text-align: center; padding: 80px 34px 0; }
  .about-title { font-family: "EB Garamond", serif; font-weight: 400; font-size: 38px; color: var(--ink); }
  .about-kicker { font-family: "Playfair Display", serif; font-style: italic; font-size: 19px; color: var(--ink); margin-top: 24px; }
  .about-text { font-family: "Raleway", sans-serif; font-size: 19px; line-height: 37px; color: var(--ink-soft); margin-top: 22px; }
</style>
</head>
<body>
<main class="stage">
  <section class="screen screen--home">
    <header class="site-header">
      <span class="brand">BLOOM BEAUTY HUB</span>
      <svg class="menu-icon" width="32" height="30" viewBox="0 0 32 30" aria-label="Menu">
        <rect x="0" y="0" width="32" height="3" fill="#1f1b19"/>
        <rect x="0" y="13" width="32" height="3" fill="#1f1b19"/>
        <rect x="0" y="26" width="32" height="3" fill="#1f1b19"/>
      </svg>
    </header>
    <div class="hero-band">
      <h1 class="hero-title">BLOOM BEAUTY HUB</h1>
      <p class="hero-sub">Education &amp; Business Mentoring for Beauty Salon Owners made simple.</p>
    </div>
    <div class="hero-art" role="img" aria-label="Illustration of a salon owner standing with folded arms beside an open door sign and a potted aloe plant"></div>
  </section>

  <section class="screen screen--about">
    <div class="top-strip"></div>
    <div class="feature-band">
      <div class="feature-art" role="img" aria-label="Round illustration of a salon owner at her shop door with an open sign and a plant"></div>
      <h2 class="feature-title">LAUNCH PAD PARLOUR</h2>
      <p class="feature-text">All the help you need to start you own salon.</p>
    </div>
    <div class="about">
      <h2 class="about-title">ABOUT US</h2>
      <p class="about-kicker">Bloom Beauty Hub</p>
      <p class="about-text">Hi, we’re ‘Bloom Beauty Hub’ and we’ve generated tens of thousands of dollars in bookings for businesses in the Beauty Industry in as little as two months using Chatterbook &amp; Snapgram Advertising.</p>
    </div>
  </section>
</main>
</body>
</html>
```